Local massage therapist needs some new marketing material

Hi there! I am a massage therapist here in Denver, CO in Alder Bend(shopping and art district) of the city. My business is called Lumo Bodywork of Denver. My practice has an eastern influence and I do reflexology, thai massage and use Chinese herbs, etc. I know all my clients and pay close attention to details. I am also very respectful of tradition and it shows in how I work. I tend to like modern, clean, fun, Asian designs. I am wanting a new business card and brochure. I have a logo and branding for my business that I want used in the design. Currently, the sign for my building is purple and I think my logo was designed to be purple. I will attach pictures of it and can send whatever files are necessary so it can be integrated into the brochure, etc. I like the purple but open to using other colors as well. Thanks!
My website is lumobodyworkofdenver.example where info can be gathered about me and services/fees for brochure.
Updates

Just increased budget. Please see new feedback in discussion thread.

Thanks!

                                       HEY ALL,

Just wanted to let you know that I made a change to my website. It is on the Prices Page. I no longer have the frequent  flyer prices but I added discounts. Let me know if you have any questions. Thanks so much!

Target Market(s)

healthy, urban, educated, upper middle class, yogis

Industry/Entity Type

Marketing

Requirements
Must have
• logo stays purple
Should not have
• not too busy

```html
<!DOCTYPE html>
<html lang="en">
<head>
<meta charset="utf-8">
<title>Lumo Bodywork of Denver – Brochure</title>
<link rel="stylesheet" href="https://fonts.googleapis.com/css2?family=Lato:ital,wght@0,300;0,400;0,700;1,400;1,700;1,900&display=swap">
<style>
  :root {
    --purple: #6a2e94;
    --purple-text: #6b3794;
    --slate: #58585a;
    --ink: #4a4a4a;
    --paper: #ffffff;
    --stage: #dcdde0;
    --rule: #e2e2e2;
  }
  * { box-sizing: border-box; margin: 0; padding: 0; }
  html, body { width: 1200px; height: 950px; overflow: hidden; }
  body { background: var(--stage); font-family: "Lato", Arial, sans-serif; }

  .brochure {
    position: absolute; left: 20px; top: 27px;
    width: 1160px; height: 896px;
    background: var(--paper);
    box-shadow: 0 4px 14px rgba(0,0,0,.25);
  }
  .fold { position: absolute; top: 0; bottom: 0; width: 1px; background: var(--rule); }
  .fold--one { left: 385px; }
  .fold--two { left: 772px; }

  .benefits {
    position: absolute; left: 10px; top: 10px; width: 367px; height: 624px;
    background: var(--slate); color: #fff; padding: 26px 20px 0 22px;
  }
  .benefits__title { font-style: italic; font-weight: 900; font-size: 25px; letter-spacing: .5px; margin-bottom: 14px; }
  .benefits__list { list-style: none; }
  .benefits__list li {
    position: relative; padding-left: 22px; font-style: italic; font-weight: 700;
    font-size: 18.5px; line-height: 22px; margin-bottom: 14px;
  }
  .benefits__list li::before { content: "+"; position: absolute; left: 0; font-weight: 400; }

  .photo { position: absolute; }
  .photo--reflexology {
    left: 10px; top: 638px; width: 367px; height: 250px;
    background: linear-gradient(135deg, #e7c8ae 0%, #f4efe6 40%, #d9e6b4 70%, #e9d3c0 100%);
  }
  .photo--stones {
    left: 396px; top: 167px; width: 758px; height: 468px;
    background: linear-gradient(100deg, #e6c3aa 0%, #d9a887 35%, #b64a3e 60%, #d8a77a 80%, #b07f5a 100%);
  }

  .wordmark {
    position: absolute; color: var(--purple-text); font-weight: 300;
    font-size: 46px; letter-spacing: 8px; line-height: 1;
  }
  .wordmark--inner { left: 440px; top: 72px; }
  .brand-right { position: absolute; left: 835px; top: 58px; display: flex; align-items: center; gap: 16px; }
  .brand-right .wordmark { position: static; }
  .brand-right__dot { width: 72px; height: 72px; border: 3px solid var(--purple); border-radius: 50%; }

  .seal {
    position: absolute; left: 566px; top: 282px; width: 84px; height: 84px;
    border-radius: 50%; background: rgba(255,255,255,.85);
  }
  .tagline { position: absolute; left: 430px; top: 392px; width: 300px; text-align: center; }
  .tagline__line { font-style: italic; font-weight: 700; font-size: 25px; color: var(--ink); line-height: 37px; }
  .tagline__highlight {
    display: inline-block; margin-top: 8px; background: var(--purple); color: #fff;
    font-weight: 700; font-size: 26px; padding: 4px 10px; white-space: nowrap;
  }

  .contact { position: absolute; left: 396px; top: 680px; width: 376px; color: var(--ink); }
  .contact__phone {
    margin-left: 40px; width: 308px; height: 40px; background: var(--slate); color: #fff;
    display: flex; align-items: center; justify-content: center; gap: 36px;
    font-style: italic; font-weight: 700; font-size: 24px;
  }
  .contact__lines { margin-top: 24px; font-style: italic; font-weight: 700; font-size: 18.5px; line-height: 34px; }
  .contact__row { display: flex; align-items: center; gap: 8px; }
  .contact__row--address { padding-left: 58px; }
  .contact__row--city { padding-left: 68px; }
  .contact__row--mail, .contact__row--web { padding-left: 0; }
  .icon { width: 18px; height: 18px; fill: currentColor; flex: none; }

  .cta { position: absolute; left: 772px; width: 388px; text-align: center; }
  .cta--top { top: 703px; }
  .cta__box { display: inline-block; background: var(--purple); color: #fff; font-style: italic; font-weight: 700; }
  .cta__box--small { width: 304px; height: 45px; line-height: 45px; font-size: 21px; }
  .cta__box--big { width: 280px; height: 47px; line-height: 47px; font-size: 29px; margin-top: 7px; }
  .web-right {
    position: absolute; left: 772px; top: 852px; width: 388px; text-align: center;
    color: var(--purple-text); font-style: italic; font-weight: 700; font-size: 19px;
  }
</style>
</head>
<body>
<main class="brochure">
  <span class="fold fold--one"></span>
  <span class="fold fold--two"></span>

  <section class="benefits">
    <h2 class="benefits__title">BENEFITS</h2>
    <ul class="benefits__list">
      <li>Relaxing the whole body</li>
      <li>Loosening and relieving tired, aching and tight muscles</li>
      <li>Increasing flexibility and range of motion</li>
      <li>Diminishing chronic pain</li>
      <li>Calming the nervous system</li>
      <li>Lowering blood pressure and heart rate</li>
      <li>Enhancing skin tone</li>
      <li>Aiding in recovery following injuries and illness</li>
      <li>Strengthening the immune system</li>
      <li>Reducing headaches and mental stress</li>
      <li>Improving relaxation</li>
      <li>Promoting restful sleep</li>
    </ul>
  </section>
  <div class="photo photo--reflexology" role="img" aria-label="Photo of hands giving a reflexology foot massage on a white towel"></div>

  <div class="wordmark wordmark--inner">LUMO</div>
  <div class="photo photo--stones" role="img" aria-label="Photo of a client relaxing on a red massage table with hot stones along the back"></div>
  <span class="seal"></span>
  <div class="tagline">
    <p class="tagline__line">May You Awaken</p>
    <p class="tagline__line">to The Light of</p>
    <span class="tagline__highlight">Your Own True Nature</span>
  </div>

  <section class="contact">
    <div class="contact__phone">
      <svg class="icon" viewBox="0 0 24 24" aria-hidden="true"><path d="M6.6 10.8a15 15 0 0 0 6.6 6.6l2.2-2.2a1 1 0 0 1 1-.25 11.4 11.4 0 0 0 3.6.57 1 1 0 0 1 1 1V20a1 1 0 0 1-1 1A17 17 0 0 1 3 4a1 1 0 0 1 1-1h3.5a1 1 0 0 1 1 1c0 1.25.2 2.45.57 3.57a1 1 0 0 1-.25 1z"/></svg>
      <span>303.555.0184</span>
    </div>
    <div class="contact__lines">
      <p class="contact__row contact__row--address">
        <svg class="icon" viewBox="0 0 24 24" aria-hidden="true"><path d="M12 2a7 7 0 0 0-7 7c0 5.2 7 13 7 13s7-7.8 7-13a7 7 0 0 0-7-7zm0 9.5A2.5 2.5 0 1 1 12 6.5a2.5 2.5 0 0 1 0 5z"/></svg>
        <span>1480 E Alder Ave,</span>
      </p>
      <p class="contact__row contact__row--city">Denver, CO 80206</p>
      <p class="contact__row contact__row--mail">
        <svg class="icon" viewBox="0 0 24 24" aria-hidden="true"><path d="M2 5h20v14H2zm2 2v.5l8 5 8-5V7zm0 2.8V17h16V9.8l-8 5z"/></svg>
        <span>info@lumobodyworkofdenver.example</span>
      </p>
      <p class="contact__row contact__row--web">
        <svg class="icon" viewBox="0 0 24 24" aria-hidden="true"><path d="M12 2a10 10 0 1 0 0 20 10 10 0 0 0 0-20zm6.9 6h-3a15 15 0 0 0-1.3-3.9A8 8 0 0 1 18.9 8zM12 4c.8 1.2 1.5 2.5 1.9 4h-3.8c.4-1.5 1.1-2.8 1.9-4zM4.3 14a8 8 0 0 1 0-4h3.4a16 16 0 0 0 0 4zm.8 2h3a15 15 0 0 0 1.3 3.9A8 8 0 0 1 5.1 16zm3-8h-3a8 8 0 0 1 4.3-3.9A15 15 0 0 0 8.1 8zM12 20c-.8-1.2-1.5-2.5-1.9-4h3.8c-.4 1.5-1.1 2.8-1.9 4zm2.3-6H9.7a14 14 0 0 1 0-4h4.6a14 14 0 0 1 0 4zm.3 5.9A15 15 0 0 0 15.9 16h3a8 8 0 0 1-4.3 3.9zM16.3 14a16 16 0 0 0 0-4h3.4a8 8 0 0 1 0 4z"/></svg>
        <span>lumobodyworkofdenver.example</span>
      </p>
    </div>
  </section>

  <div class="brand-right">
    <span class="brand-right__dot"></span>
    <span class="wordmark">LUMO</span>
  </div>
  <div class="cta cta--top">
    <span class="cta__box cta__box--small">YOUR PATH TO WELLNESS</span><br>
    <span class="cta__box cta__box--big">BEGINS HERE!</span>
  </div>
  <p class="web-right">lumobodyworkofdenver.example</p>
</main>
</body>
</html>
```